Northfield Builders Guild Business card

We are looking for a new business card design with photo included.
Our business is a nonprofit construction contractor membership organization. We offer business education, assist with business setup and licensing, provide safety training, and provide a member directory.
URL: www.builderslinkguild.org
Color code:
CMYK: 0 cyan, 42 magenta, 100 yellow, 0 black for Print.
Hexidecimal: #FF9900
RGB: R 255; G 153; B 0

```html
<!DOCTYPE html>
<html lang="en">
<head>
<meta charset="utf-8">
<title>Northfield Builders Guild Business Card</title>
<link href="https://fonts.googleapis.com/css2?family=Montserrat:wght@400;500;600;800&display=swap" rel="stylesheet">
<style>
  :root {
    --orange: #FF9900;
    --ink: #2b2b2b;
    --ink-soft: #3a3a3a;
    --paper: #f7f7f5;
    --card-dark: #2e2e2f;
    --stage: #1f1f20;
    --photo-top: #d9d4cf;
    --photo-bottom: #3a3230;
  }
  * { box-sizing: border-box; margin: 0; padding: 0; }
  html, body { width: 1200px; height: 900px; overflow: hidden; }
  body {
    background: var(--stage);
    font-family: "Montserrat", Arial, sans-serif;
    position: relative;
  }
  .card {
    position: absolute;
    width: 560px;
    height: 320px;
    overflow: hidden;
    box-shadow: 0 18px 40px rgba(0,0,0,0.55);
  }
  .card-front { left: 150px; top: 90px; background: var(--paper); }
  .card-back { left: 490px; top: 480px; background: var(--card-dark); }

  .front-bands { position: absolute; inset: 0; width: 100%; height: 100%; }

  .identity { position: absolute; left: 40px; top: 46px; }
  .person-name { font-weight: 600; font-size: 19px; letter-spacing: 0.3px; color: var(--ink); }
  .person-name .surname { color: var(--orange); }
  .person-role { font-size: 13px; color: var(--ink-soft); margin-top: 4px; }

  .contact-list { position: absolute; left: 40px; top: 110px; list-style: none; }
  .contact-list li {
    display: flex; align-items: center; gap: 9px;
    font-size: 12.5px; color: var(--ink-soft); line-height: 20px;
  }
  .contact-list svg { width: 13px; height: 13px; flex: none; }

  .address { position: absolute; left: 40px; top: 186px; font-size: 12.5px; line-height: 18px; color: var(--ink-soft); }

  .brand-mark { position: absolute; left: 40px; top: 248px; display: flex; align-items: center; gap: 8px; }
  .brand-square { width: 14px; height: 14px; background: var(--orange); }
  .brand-name { font-weight: 800; font-size: 17px; color: var(--ink); letter-spacing: 0.2px; }

  .portrait {
    position: absolute; left: 352px; top: 24px; width: 170px; height: 236px;
    background: linear-gradient(180deg, var(--photo-top) 0%, var(--photo-top) 22%, var(--photo-bottom) 60%, var(--photo-bottom) 100%);
  }

  .back-mark {
    position: absolute; inset: 0;
    display: flex; align-items: center; justify-content: center; gap: 12px;
  }
  .back-mark .brand-square { width: 20px; height: 20px; }
  .back-mark .brand-name { font-size: 28px; color: var(--orange); }
</style>
</head>
<body>
  <section class="card card-front">
    <svg class="front-bands" viewBox="0 0 560 320" preserveAspectRatio="none" aria-hidden="true">
      <polygon points="318,282 560,262 560,272 312,292" fill="var(--orange)"/>
      <polygon points="0,306 300,286 294,296 0,316" fill="var(--ink)"/>
      <rect x="0" y="316" width="560" height="4" fill="var(--ink)"/>
    </svg>

    <div class="identity">
      <p class="person-name">JORDAN <span class="surname">WHITFIELD</span></p>
      <p class="person-role">Director</p>
    </div>

    <ul class="contact-list">
      <li>
        <svg viewBox="0 0 24 24" fill="none" stroke="var(--orange)" stroke-width="2"><path d="M5 3h4l2 5-3 2a12 12 0 0 0 6 6l2-3 5 2v4a2 2 0 0 1-2 2A18 18 0 0 1 3 5a2 2 0 0 1 2-2z"/></svg>
        (555) 210-3847
      </li>
      <li>
        <svg viewBox="0 0 24 24" fill="none" stroke="var(--orange)" stroke-width="2"><rect x="3" y="5" width="18" height="14"/><path d="M3 6l9 7 9-7"/></svg>
        info@builderslinkguild.org
      </li>
      <li>
        <svg viewBox="0 0 24 24" fill="none" stroke="var(--orange)" stroke-width="2"><circle cx="12" cy="12" r="9"/><path d="M3 12h18M12 3c3 3 3 15 0 18M12 3c-3 3-3 15 0 18"/></svg>
        builderslinkguild.org
      </li>
    </ul>

    <p class="address">2400 Cedar Mill Avenue<br>Northfield, OR 97000</p>

    <div class="brand-mark">
      <span class="brand-square"></span>
      <span class="brand-name">Northfield Builders Guild</span>
    </div>

    <div class="portrait" role="img" aria-label="Portrait photo of the director in a dark blazer"></div>
  </section>

  <section class="card card-back">
    <div class="back-mark">
      <span class="brand-square"></span>
      <span class="brand-name">Northfield Builders Guild</span>
    </div>
  </section>
</body>
</html>
```